Website for "Bright Morrow Ltd" cleaning bsuiness

We require a website to expose our business to the local market. We want to provide background on who we are and what we do but in an easily digestible way. We clean domestic and commercial premises and want to provide a list of all of our services to potential customers. We operate out of Warrington in the UK.

We would like the website to be animated in some way so that the experience of using it is not dull or mundane. This website needs to be an extension of our company.

Target Market(s)

30 - 60 year olds for Domestic plus commercial clients

Industry/Entity Type

Cleaning Service

Coding

Coded - Design and coding required

Number of Pages Required

4 page

Font styles to use
Sans Serif

Colors
0455a3
3176b5
85acd3
cfdeed
ffffff
000000
1b1b1b
c8c8c8
757575

Requirements
Must have
• Logo which has been provided. Theme based around the logo and its colours. Simple layout to avoid confusion.
Nice to have
• Animations where possible to impress the customer.
Should not have
• any pictures of cleaning equipment, fairies, maids etc

```html
<!DOCTYPE html>
<html lang="en">
<head>
<meta charset="utf-8">
<title>Bright Morrow Ltd – Contact Us</title>
<link href="https://fonts.googleapis.com/css2?family=Raleway:wght@300;400;600;700&family=Arimo:wght@400;700&display=swap" rel="stylesheet">
<style>
  :root {
    --brand: #0455a3;
    --brand-mid: #3176b5;
    --brand-soft: #85acd3;
    --brand-pale: #cfdeed;
    --white: #ffffff;
    --ink: #1b1b1b;
    --ink-soft: #4a4a4a;
    --grey: #757575;
    --line: #c8c8c8;
    --field: #f6f6f6;
  }
  * { box-sizing: border-box; margin: 0; padding: 0; }
  html, body { width: 830px; height: 1200px; overflow: hidden; background: var(--white); }
  body { font-family: "Arimo", Arial, sans-serif; color: var(--ink); }
  .page { position: relative; width: 830px; height: 1200px; overflow: hidden; }

  .hero-art { position: absolute; left: 0; top: 0; width: 830px; height: 480px; }

  .main-nav { position: absolute; top: 0; left: 0; width: 830px; height: 54px; }
  .main-nav .rule { position: absolute; left: 230px; right: 0; top: 53px; height: 1px; background: #8d9aa6; }
  .main-nav ul { list-style: none; }
  .main-nav li { position: absolute; top: 21px; font-size: 12.6px; letter-spacing: .2px; color: #2a2a2a; }
  .main-nav li.active { color: var(--brand); }
  .main-nav li.active::after { content: ""; position: absolute; left: -9px; right: -9px; top: 30px; height: 3px; background: var(--brand); }

  .brand-mark { position: absolute; left: 0; width: 830px; top: 180px; text-align: center; }
  .brand-mark .name { font-family: "Raleway", sans-serif; font-weight: 700; font-size: 52px; color: var(--brand); letter-spacing: .5px; }
  .brand-mark .dot { display: inline-block; width: 18px; height: 18px; border-radius: 50%; background: var(--brand-mid); margin-right: 12px; vertical-align: 6px; }
  .brand-mark .tagline { font-family: "Raleway", sans-serif; font-size: 17px; color: var(--ink); margin-top: 10px; letter-spacing: 1px; }

  .section-title { position: absolute; top: 490px; left: 0; width: 830px; text-align: center; font-family: "Raleway", sans-serif; font-weight: 400; font-size: 29px; color: #2b2b2b; }
  .section-title span { color: var(--brand); }

  .col-title { position: absolute; top: 540px; font-family: "Raleway", sans-serif; font-weight: 400; font-size: 19px; color: var(--brand); }

  .info-list { position: absolute; list-style: none; font-size: 10.5px; color: var(--ink-soft); line-height: 19px; }
  .info-list li { position: relative; padding-left: 28px; }
  .info-list svg { position: absolute; left: 0; top: 2px; width: 16px; height: 14px; }
  .contact-info { left: 53px; top: 578px; width: 200px; }
  .contact-info li + li { margin-top: 8px; }

  .map-area { position: absolute; left: 53px; top: 704px; width: 335px; height: 156px; background: linear-gradient(100deg, #a8c8f0 0%, #b9d2ef 30%, #e7e3d6 55%, #ece7d8 100%); }

  .contact-form { position: absolute; left: 437px; top: 576px; width: 331px; }
  .contact-form .field { width: 331px; height: 32px; border: 1px solid var(--line); background: var(--field); margin-bottom: 15px; font-family: inherit; font-size: 10.5px; color: var(--ink-soft); padding: 0 9px; display: flex; align-items: center; }
  .contact-form .field.message { height: 79px; align-items: flex-start; padding-top: 9px; }
  .btn { display: inline-flex; align-items: center; justify-content: center; background: var(--brand); color: var(--white); font-family: "Arimo", Arial, sans-serif; font-size: 14px; border: 0; }
  .contact-form .btn { width: 91px; height: 39px; margin-top: 0; }

  .footer-art { position: absolute; left: 0; top: 910px; width: 830px; height: 250px; }
  .footer-brand { position: absolute; left: 56px; top: 1030px; width: 160px; }
  .footer-brand .name { font-family: "Raleway", sans-serif; font-weight: 700; font-size: 22px; color: var(--brand); line-height: 26px; }
  .footer-brand .dot { display: inline-block; width: 10px; height: 10px; border-radius: 50%; background: var(--brand-mid); margin-right: 6px; vertical-align: 2px; }
  .footer-brand .tagline { font-family: "Raleway", sans-serif; font-size: 10px; color: var(--ink); margin-top: 6px; }

  .footer-heading { position: absolute; top: 996px; font-family: "Raleway", sans-serif; font-weight: 700; font-size: 13px; color: var(--brand); letter-spacing: .2px; }
  .link-list { position: absolute; left: 243px; top: 1021px; list-style: none; font-size: 10.5px; color: var(--ink-soft); }
  .link-list li { position: relative; padding-left: 15px; height: 18.8px; }
  .link-list li::before { content: ""; position: absolute; left: 0; top: 4px; width: 5px; height: 5px; border: 1px solid var(--brand); }
  .link-list li.active::before { background: var(--brand); }
  .footer-info { left: 419px; top: 1022px; width: 165px; }
  .footer-info li { padding-left: 27px; }
  .footer-info li + li { margin-top: 8px; }

  .newsletter { position: absolute; left: 605px; top: 1022px; width: 180px; font-size: 10.5px; color: var(--ink-soft); line-height: 16px; }
  .newsletter .field { width: 173px; height: 29px; border: 1px solid var(--line); background: var(--white); margin: 11px 0 0 -2px; padding: 0 8px; display: flex; align-items: center; }
  .newsletter .btn { width: 108px; height: 29px; margin: 6px 0 0 -2px; }

  .site-bottom { position: absolute; left: 0; top: 1160px; width: 830px; height: 40px; background: var(--brand); color: var(--brand-pale); font-size: 10.5px; display: flex; align-items: center; justify-content: center; }
  .site-bottom strong { color: var(--white); margin: 0 4px; }
</style>
</head>
<body>
<div class="page">

  <svg class="hero-art" viewBox="0 0 830 480" role="img" aria-label="Bright white living room and glass-walled office interior">
    <defs>
      <linearGradient id="heroFill" x1="0" y1="0" x2="1" y2="1">
        <stop offset="0" stop-color="#e9ecef"/>
        <stop offset=".45" stop-color="#f1f3f5"/>
        <stop offset="1" stop-color="#dde5ec"/>
      </linearGradient>
      <linearGradient id="heroWarm" x1="0" y1="0" x2="0" y2="1">
        <stop offset=".6" stop-color="#ffffff" stop-opacity="0"/>
        <stop offset="1" stop-color="#d7c7b3" stop-opacity=".55"/>
      </linearGradient>
      <linearGradient id="bandFade" x1="0" y1="0" x2="1" y2="0">
        <stop offset="0" stop-color="#0455a3"/>
        <stop offset=".7" stop-color="#0455a3"/>
        <stop offset="1" stop-color="#85acd3"/>
      </linearGradient>
    </defs>
    <polygon points="0,0 830,0 830,472 416,396 0,468" fill="url(#heroFill)"/>
    <polygon points="0,0 830,0 830,472 416,396 0,468" fill="url(#heroWarm)"/>
    <polyline points="0,472 416,399 830,476" fill="none" stroke="url(#bandFade)" stroke-width="7"/>
  </svg>

  <nav class="main-nav">
    <div class="rule"></div>
    <ul>
      <li class="active" style="left:243px">HOME</li>
      <li style="left:325px">ABOUT US</li>
      <li style="left:418px">SERVICES</li>
      <li style="left:510px">BLOG</li>
      <li style="left:574px">CONTACT US</li>
    </ul>
  </nav>

  <div class="brand-mark">
    <div class="name"><span class="dot"></span>Bright Morrow</div>
    <div class="tagline">Professional Cleaning Service</div>
  </div>

  <h1 class="section-title">CONTACT <span>US</span></h1>

  <h2 class="col-title" style="left:54px">Contact Info</h2>
  <h2 class="col-title" style="left:432px">Get In Touch With Us</h2>

  <ul class="info-list contact-info">
    <li><svg viewBox="0 0 16 14"><path d="M1 2.5 5.5 1 10.5 2.5 15 1v10.5L10.5 13 5.5 11.5 1 13z M5.5 1v10.5 M10.5 2.5V13" fill="none" stroke="#0455a3" stroke-width="1.1" stroke-linejoin="round"/></svg>101- Lorem ipsum is simple dummy text of print and type setting industry</li>
    <li><svg viewBox="0 0 16 14"><path d="M3 1.2 5.4 3.6 4.2 5.3c.9 1.9 2.4 3.4 4.3 4.3l1.7-1.2 2.4 2.4-1.6 1.8C6.4 12.3 1.7 7.6 1.4 2.8z" fill="none" stroke="#0455a3" stroke-width="1.1" stroke-linejoin="round"/></svg>0161 555 0198</li>
    <li><svg viewBox="0 0 16 14"><rect x="1" y="2" width="14" height="10" rx="1" fill="none" stroke="#0455a3" stroke-width="1.3"/><path d="M1.5 2.8 8 8l6.5-5.2" fill="none" stroke="#0455a3" stroke-width="1.3"/></svg>info@brightmorrowltd.com</li>
  </ul>

  <div class="map-area" role="img" aria-label="Map showing the business location"></div>

  <form class="contact-form">
    <div class="field">Enter Name</div>
    <div class="field">Enter Email</div>
    <div class="field">Enter Contact No.</div>
    <div class="field message">Enter Message</div>
    <span class="btn">SUBMIT</span>
  </form>

  <svg class="footer-art" viewBox="0 0 830 250" role="img" aria-label="Soft background photo of a smiling woman resting on a white carpet">
    <defs>
      <linearGradient id="footFill" x1="0" y1="0" x2="1" y2="0">
        <stop offset="0" stop-color="#f6f2ee"/>
        <stop offset=".4" stop-color="#f3ebe4"/>
        <stop offset=".75" stop-color="#f8f8f8"/>
        <stop offset="1" stop-color="#f7f7f7"/>
      </linearGradient>
    </defs>
    <polygon points="0,83 416,7 830,83 830,250 0,250" fill="url(#footFill)"/>
    <polyline points="0,86 416,8 830,85" fill="none" stroke="#0455a3" stroke-width="7"/>
  </svg>

  <div class="footer-brand">
    <div class="name"><span class="dot"></span>Bright Morrow</div>
    <div class="tagline">Professional Cleaning Service</div>
  </div>

  <h3 class="footer-heading" style="left:244px">USEFULL LINKS</h3>
  <ul class="link-list">
    <li class="active">Home</li>
    <li>About Us</li>
    <li>Services</li>
    <li>Blog</li>
    <li>Contact Us</li>
  </ul>

  <h3 class="footer-heading" style="left:421px">GET IN TOUCH</h3>
  <ul class="info-list footer-info">
    <li><svg viewBox="0 0 16 14"><path d="M1 2.5 5.5 1 10.5 2.5 15 1v10.5L10.5 13 5.5 11.5 1 13z M5.5 1v10.5 M10.5 2.5V13" fill="none" stroke="#0455a3" stroke-width="1.1" stroke-linejoin="round"/></svg>101- Lorem ipsum is simple dummy text of print and type setting industry</li>
    <li><svg viewBox="0 0 16 14"><path d="M3 1.2 5.4 3.6 4.2 5.3c.9 1.9 2.4 3.4 4.3 4.3l1.7-1.2 2.4 2.4-1.6 1.8C6.4 12.3 1.7 7.6 1.4 2.8z" fill="none" stroke="#0455a3" stroke-width="1.1" stroke-linejoin="round"/></svg>0161 555 0198</li>
    <li><svg viewBox="0 0 16 14"><rect x="1" y="2" width="14" height="10" rx="1" fill="none" stroke="#0455a3" stroke-width="1.3"/><path d="M1.5 2.8 8 8l6.5-5.2" fill="none" stroke="#0455a3" stroke-width="1.3"/></svg>info@brightmorrowltd.com</li>
  </ul>

  <h3 class="footer-heading" style="left:605px">NEWSLETTER</h3>
  <div class="newsletter">
    <p>Would you like to receive exclusive access to articles, white papers and our regular monthly newsletter?</p>
    <div class="field">Enter Email Id</div>
    <span class="btn">SUBMIT</span>
  </div>

  <footer class="site-bottom">© 2016 <strong>Bright Morrow -</strong> All rights reserved.</footer>
</div>
</body>
</html>
```